bird wings, breathing, coaching, rhythm, heart

I would like this card design to be inspired by the following Rumi poem - now that I see some cards with the poem on it, I am pretty sure I don't want that. The feel of the cards should be watery and emotional, one of rhythm, breathing like a pendulum. An Ouroboros, (alchemical imagery in general), Birds, lungs, bird wings, hands, clouds, water, waves and rivers are all good images. Simple elegance is appreciated.
Cards should contain my name, title (coach), address, phone number and email address.
Your grief for what you've lost lifts a mirror
up to where you're bravely working.
Expecting the worst, you look, and instead,
here's the joyful face you've been wanting to see.
Your hand opens and closes and opens and closes.
If it were always a fist or always stretched open,
you would be paralyzed.
Your deepest presence
is in every small contracting and expanding,
the two as beautifully balanced and coordinated
as birdwings.
Contact Information for Business Card
Dorran Pelkwith, MA
Coach
4718 Varno St.
Berkeley, CA 94188
415-382-6649
pelkwith@mailvaro.net
Designer to choose colors to be used in the design.

```html
<!DOCTYPE html>
<html lang="en">
<head>
<meta charset="utf-8">
<title>Dorran Pelkwith, MA — Coach — Business Card</title>
<link rel="stylesheet" href="https://fonts.googleapis.com/css2?family=Lato:wght@300;400;700&display=swap">
<style>
  :root {
    --stage: #505050;
    --paper-front: #f7f7f7;
    --paper-back: #ffffff;
    --lagoon: #5cdfc4;
    --ink: #2a2a2a;
    --on-lagoon: #ffffff;
  }
  * { margin: 0; padding: 0; box-sizing: border-box; }
  html, body {
    width: 1200px; height: 802px; overflow: hidden;
    background: var(--stage);
    font-family: "Lato", sans-serif;
  }
  .stage { position: relative; width: 1200px; height: 802px; }
  .card {
    position: absolute; top: 274px;
    width: 443px; height: 265px; overflow: hidden;
    box-shadow: 0 2px 6px rgba(0,0,0,0.35);
  }
  .card--front { left: 136px; background: var(--paper-front); }
  .card--back  { left: 624px; background: var(--paper-back); }
  .card__wave { position: absolute; inset: 0; width: 100%; height: 100%; }
  .card__wave path { fill: var(--lagoon); }

  .identity { position: absolute; left: 26px; top: 55px; }
  .identity__name {
    color: var(--lagoon); font-size: 16.5px; font-weight: 700;
    letter-spacing: -0.2px; line-height: 1.3;
  }
  .identity__title { color: var(--ink); font-size: 17px; font-weight: 400; line-height: 1.3; margin-top: 1px; }

  .contact {
    position: absolute; right: 23px; top: 134px;
    color: var(--on-lagoon); text-align: right; font-style: normal;
    font-size: 16.5px; font-weight: 300; line-height: 19.5px;
  }
  .contact__address { margin-bottom: 21px; }
  .contact__line { display: flex; justify-content: flex-end; align-items: center; gap: 2px; }
  .contact__icon { width: 12px; height: 12px; fill: var(--on-lagoon); flex: none; }
</style>
</head>
<body>
<main class="stage">
  <section class="card card--front" aria-label="Business card front">
    <svg class="card__wave" viewBox="0 0 443 265" preserveAspectRatio="none" aria-hidden="true">
      <path d="M246 0 H443 V265 H124 C195 225 245 160 258 95 C266 60 262 25 246 0 Z"/>
    </svg>
    <div class="identity">
      <h1 class="identity__name">DORRAN PELKWITH, MA</h1>
      <p class="identity__title">Coach</p>
    </div>
    <address class="contact">
      <div class="contact__address">4718 Varno St.<br>Berkeley, CA 94188</div>
      <div class="contact__line">415-382-6649
        <svg class="contact__icon" viewBox="0 0 12 12" aria-hidden="true"><path d="M1 4.5 C1 2 3 1 6 1 C9 1 11 2 11 4.5 H8.6 V3.4 H3.4 V4.5 Z M3 5.2 H9 L10.5 10.5 H1.5 Z"/></svg>
      </div>
      <div class="contact__line">pelkwith@mailvaro.net
        <svg class="contact__icon" viewBox="0 0 12 12" aria-hidden="true"><path d="M1 2.5 H11 V9.5 H1 Z"/><path d="M1.5 3 L6 6.6 L10.5 3" fill="none" stroke="#5cdfc4" stroke-width="1"/></svg>
      </div>
    </address>
  </section>

  <section class="card card--back" aria-label="Business card back">
    <svg class="card__wave" viewBox="0 0 443 265" preserveAspectRatio="none" aria-hidden="true">
      <path d="M391 0 H443 V265 H269 C330 238 392 170 404 95 C409 60 404 25 391 0 Z"/>
    </svg>
  </section>
</main>
</body>
</html>
```